KLV Plant Services

We are a heavy diesel mechanical business with additional air con certificates, remapping engine rebuilt

Contact Information for Business Card

Company Name, Director Name, Managing Director, Contact details, email and website

Font styles to use
Serif
Script

```html
<!DOCTYPE html>
<html lang="en">
<head>
<meta charset="utf-8">
<title>KLV Plant Services – Business Card</title>
<link href="https://fonts.googleapis.com/css2?family=Arimo:wght@400;700&display=swap" rel="stylesheet">
<style>
  :root {
    --stage: #e4e5e7;
    --card: #ffffff;
    --navy: #27246b;
    --ink: #111111;
    --text: #1c1c1c;
    --photo-light: #c9b25a;
    --photo-mid: #8a7a45;
    --photo-dark: #4b4438;
  }
  html, body {
    margin: 0;
    padding: 0;
    width: 1200px;
    height: 780px;
    overflow: hidden;
    background: var(--stage);
    font-family: "Arimo", Arial, sans-serif;
  }
  .canvas {
    position: relative;
    width: 1200px;
    height: 780px;
  }
  .card {
    position: absolute;
    width: 500px;
    height: 286px;
    background: var(--card);
    border-radius: 22px;
    overflow: hidden;
    box-shadow: 0 6px 18px rgba(0,0,0,0.18);
  }
  .card--back { left: 70px; top: 90px; }
  .card--front { left: 630px; top: 404px; }

  .wordmark {
    display: flex;
    align-items: center;
    gap: 12px;
    color: var(--navy);
    font-weight: 700;
    white-space: nowrap;
  }
  .wordmark__dot {
    border: 4px solid var(--ink);
    border-radius: 50%;
    flex: none;
  }
  .card--back .wordmark {
    position: absolute;
    left: 0; right: 0; top: 0; bottom: 0;
    justify-content: center;
    font-size: 40px;
  }
  .card--back .wordmark__dot { width: 44px; height: 44px; }

  .card__photo {
    position: absolute;
    left: 0; top: 0;
    width: 500px;
    height: 286px;
  }
  .card--front .wordmark {
    position: absolute;
    left: 28px;
    top: 58px;
    font-size: 19px;
    gap: 8px;
  }
  .card--front .wordmark__dot { width: 20px; height: 20px; border-width: 3px; }

  .contact {
    position: absolute;
    left: 28px;
    top: 118px;
    color: var(--text);
  }
  .contact__name {
    margin: 0;
    font-size: 19px;
    letter-spacing: 0.5px;
    font-weight: 400;
    color: var(--navy);
  }
  .contact__name strong { color: var(--ink); font-weight: 700; }
  .contact__role { margin: 2px 0 8px; font-size: 12px; }
  .contact__phone { margin: 0 0 10px; font-size: 16px; }
  .contact__line { margin: 0; font-size: 13px; line-height: 17px; }
  .contact__address { margin-top: 10px; }
</style>
</head>
<body>
<main class="canvas">
  <section class="card card--back" aria-label="Business card back">
    <div class="wordmark"><span class="wordmark__dot"></span>KLV Plant Services</div>
  </section>

  <section class="card card--front" aria-label="Business card front">
    <svg class="card__photo" viewBox="0 0 500 286" aria-hidden="false">
      <defs>
        <linearGradient id="workshopTones" x1="0" y1="0" x2="1" y2="1">
          <stop offset="0" stop-color="#7a6a4e"/>
          <stop offset="0.45" stop-color="var(--photo-light)"/>
          <stop offset="0.75" stop-color="var(--photo-mid)"/>
          <stop offset="1" stop-color="var(--photo-dark)"/>
        </linearGradient>
      </defs>
      <path d="M286,0 Q238,170 500,262 L500,0 Z" fill="#000"/>
      <path d="M300,0 Q256,162 500,250 L500,0 Z" fill="url(#workshopTones)"
            role="img" aria-label="Photo of yellow heavy machinery being serviced in a workshop"/>
    </svg>

    <div class="wordmark"><span class="wordmark__dot"></span>KLV Plant Services</div>

    <div class="contact">
      <h1 class="contact__name">MARK <strong>ELLISON</strong></h1>
      <p class="contact__role">Managing Director</p>
      <p class="contact__phone">(615) 555-0142</p>
      <p class="contact__line">office@klvplantservices.com</p>
      <p class="contact__line">www.klvplantservices.com</p>
      <p class="contact__line contact__address">48 C Harlan St Nashville, TN 37204</p>
    </div>
  </section>
</main>
</body>
</html>
```